Business Card Design Project - 2 sided

We need a business card design for a card having one business on each side (ie. two businesses on one card). Would like a design that incorporates logo, tagline and normal fields (name, position, address, phone).

Would also like an allowance for small font text along the bottom (text to be determined, but less than 50 characters).

NB. Attached logo for Harbor Quill has two variations - either can be used.

www.harborquill-example.com / www.velmaro-example.com

```html
<!DOCTYPE html>
<html lang="en">
<head>
<meta charset="utf-8">
<title>Business Cards – Harbor Quill / Velmaro</title>
<link rel="stylesheet" href="https://fonts.googleapis.com/css2?family=Open+Sans:wght@400;600;700&display=swap">
<style>
  :root {
    --backdrop: #4a2c1a;
    --card-white: #ffffff;
    --navy: #262262;
    --sky: #3a8ac4;
    --lime: #8cc63f;
    --ink: #231f20;
    --grey-ink: #3c3c3c;
    --muted: #555555;
    --band-text: #ffffff;
  }
  * { box-sizing: border-box; margin: 0; padding: 0; }
  html, body {
    width: 1200px; height: 412px; overflow: hidden;
    background: var(--backdrop);
    font-family: "Open Sans", Arial, sans-serif;
  }
  .canvas { position: relative; width: 1200px; height: 412px; }

  .card {
    position: absolute; top: 64px;
    width: 498px; height: 284px;
    background: var(--card-white);
    overflow: hidden;
    box-shadow: 0 3px 8px rgba(0,0,0,.45);
  }
  .card--harbor { left: 74px; --accent: var(--navy); }
  .card--velmaro { left: 629px; --accent: var(--sky); }

  .card__curves { position: absolute; inset: 0; width: 498px; height: 284px; }
  .curve-accent { fill: var(--lime); }
  .curve-band { fill: var(--accent); }

  .brand {
    position: absolute; left: 0; right: 0;
    display: flex; align-items: center; justify-content: center; gap: 10px;
  }
  .brand__dot { border-radius: 50%; background: var(--lime); flex: none; }
  .brand__name { font-weight: 600; line-height: 1; }

  .card--harbor .brand { top: 34px; flex-direction: column; gap: 12px; }
  .card--harbor .brand__dot { width: 44px; height: 44px; }
  .card--harbor .brand__name { font-size: 21px; color: var(--navy); letter-spacing: .5px; }

  .card--velmaro .brand { top: 46px; }
  .card--velmaro .brand__dot { width: 40px; height: 40px; }
  .card--velmaro .brand__name { font-size: 38px; color: var(--sky); }

  .tagline {
    position: absolute; left: 0; right: 0; text-align: center;
  }
  .card--harbor .tagline { top: 110px; font-size: 10px; color: var(--ink); font-weight: 600; }
  .card--velmaro .tagline { top: 93px; font-size: 14px; color: var(--grey-ink); font-weight: 700; }

  .person {
    position: absolute; top: 135px; left: 0; right: 0; text-align: center;
    font-size: 12.5px; color: var(--muted);
  }
  .person__name { font-size: 16px; font-weight: 700; color: var(--accent); }

  .contact {
    position: absolute; left: 0; right: 0; top: 196px;
    text-align: center; color: var(--band-text);
    font-size: 12.5px; line-height: 21px;
  }
  .contact__row { display: flex; justify-content: center; align-items: center; gap: 8px; white-space: nowrap; }
  .contact__item { display: inline-flex; align-items: center; gap: 2px; }
  .icon { width: 10px; height: 10px; fill: currentColor; }
  .contact__fine { font-size: 10px; letter-spacing: .2px; }
</style>
</head>
<body>
<main class="canvas">

  <section class="card card--harbor" aria-label="Harbor Quill business card">
    <svg class="card__curves" viewBox="0 0 498 284" aria-hidden="true">
      <path class="curve-accent" d="M0,224 Q249,108 498,224 L498,228 Q249,122 0,228 Z"/>
      <path class="curve-band" d="M0,232 Q249,126 498,232 L498,284 L0,284 Z"/>
    </svg>
    <div class="brand">
      <span class="brand__dot"></span>
      <span class="brand__name">Harbor Quill</span>
    </div>
    <p class="tagline">Website Translation and Localisation Specialist...</p>
    <p class="person"><span class="person__name">Your Name</span> / Title</p>
    <div class="contact">
      <div class="contact__row">
        <span class="contact__item"><svg class="icon" viewBox="0 0 10 10"><path d="M2 0.5 L3.6 2.6 L2.8 3.6 Q4 6 6.4 7.2 L7.4 6.4 L9.5 8 L8.4 9.5 Q3.5 9 0.5 1.6 Z"/></svg>123-456-7890</span>
        <span class="contact__item"><svg class="icon" viewBox="0 0 10 10"><rect x="2.5" y="0" width="5" height="10" rx="1"/><rect x="3.3" y="1.2" width="3.4" height="6" fill="var(--navy)"/></svg>123-456-7890</span>
        <span class="contact__item"><svg class="icon" viewBox="0 0 10 10"><rect x="0" y="3" width="10" height="6" rx="1"/><rect x="2" y="0" width="6" height="3.5"/></svg>123-456-7890</span>
      </div>
      <div class="contact__row">
        <span class="contact__item"><svg class="icon" viewBox="0 0 10 10"><rect x="0" y="2" width="10" height="7" rx="1"/><path d="M0.5 2.5 L5 6 L9.5 2.5" stroke="var(--navy)" fill="none"/></svg>name@website.com</span>
        <span class="contact__item"><svg class="icon" viewBox="0 0 10 10"><circle cx="5" cy="5" r="5"/><path d="M0 5 H10 M5 0 V10" stroke="var(--navy)" stroke-width=".8"/></svg>www.website.com</span>
      </div>
      <div class="contact__row">Complex name, Street name, City, State, zip code</div>
      <div class="contact__row contact__fine">xxxxxxxxxxxxxxxxxxxxxxxxxxxxxxxxxxxxxxxxxxxxxxxxxx</div>
    </div>
  </section>

  <section class="card card--velmaro" aria-label="Velmaro business card">
    <svg class="card__curves" viewBox="0 0 498 284" aria-hidden="true">
      <path class="curve-accent" d="M0,224 Q249,108 498,224 L498,228 Q249,122 0,228 Z"/>
      <path class="curve-band" d="M0,232 Q249,126 498,232 L498,284 L0,284 Z"/>
    </svg>
    <div class="brand">
      <span class="brand__dot"></span>
      <span class="brand__name">Velmaro</span>
    </div>
    <p class="tagline">Professional SEO Services</p>
    <p class="person"><span class="person__name">Your Name</span> / Title</p>
    <div class="contact">
      <div class="contact__row">
        <span class="contact__item"><svg class="icon" viewBox="0 0 10 10"><path d="M2 0.5 L3.6 2.6 L2.8 3.6 Q4 6 6.4 7.2 L7.4 6.4 L9.5 8 L8.4 9.5 Q3.5 9 0.5 1.6 Z"/></svg>123-456-7890</span>
        <span class="contact__item"><svg class="icon" viewBox="0 0 10 10"><rect x="2.5" y="0" width="5" height="10" rx="1"/><rect x="3.3" y="1.2" width="3.4" height="6" fill="var(--sky)"/></svg>123-456-7890</span>
        <span class="contact__item"><svg class="icon" viewBox="0 0 10 10"><rect x="0" y="3" width="10" height="6" rx="1"/><rect x="2" y="0" width="6" height="3.5"/></svg>123-456-7890</span>
      </div>
      <div class="contact__row">
        <span class="contact__item"><svg class="icon" viewBox="0 0 10 10"><rect x="0" y="2" width="10" height="7" rx="1"/><path d="M0.5 2.5 L5 6 L9.5 2.5" stroke="var(--sky)" fill="none"/></svg>name@website.com</span>
        <span class="contact__item"><svg class="icon" viewBox="0 0 10 10"><circle cx="5" cy="5" r="5"/><path d="M0 5 H10 M5 0 V10" stroke="var(--sky)" stroke-width=".8"/></svg>www.website.com</span>
      </div>
      <div class="contact__row">Complex name, Street name, City, State, zip code</div>
      <div class="contact__row contact__fine">xxxxxxxxxxxxxxxxxxxxxxxxxxxxxxxxxxxxxxxxxxxxxxxxxx</div>
    </div>
  </section>

</main>
</body>
</html>
```